Copperleaf Roofing Business Card

This is my current business card. But I’d like to make some changes. Somewhere on the card I’d like to list some of the services we offer. Maybe on the back? But I’d still like to keep the red. White and black modern look.

-residential & commercial roofing
-Roof Repairs & Maintenance
-Storm Damage & Insurance Claims specialist
-Christmas Lights and permanent Christmas lights
Fencing. Windows. Gutters. Siding. Sheetrock, painting.

```html
<!DOCTYPE html>
<html lang="en">
<head>
<meta charset="utf-8">
<title>Copperleaf Roofing Co. Business Card</title>
<link rel="stylesheet" href="https://fonts.googleapis.com/css2?family=Montserrat:wght@400;500;800&family=Michroma&display=swap">
<style>
  :root {
    --stage: #2b2b2b;
    --ink: #0a0a0a;
    --paper: #ffffff;
    --red: #e0282a;
    --grey: #444444;
  }
  * { box-sizing: border-box; margin: 0; padding: 0; }
  html, body {
    width: 1200px; height: 988px; overflow: hidden;
    background: var(--stage);
    font-family: "Montserrat", sans-serif;
  }
  .stage {
    width: 1200px; height: 988px;
    display: flex; flex-direction: column; align-items: center; justify-content: center; gap: 48px;
  }
  .card {
    position: relative;
    width: 700px; height: 400px;
    border-radius: 34px;
    border-bottom: 8px solid var(--red);
    border-left: 3px solid var(--red);
    border-right: 3px solid var(--red);
    overflow: hidden;
  }
  .card--back { background: var(--ink); color: var(--paper); }
  .card--front { background: var(--paper); color: var(--ink); }

  .brand {
    position: absolute; left: 0; right: 0;
    display: flex; flex-direction: column; align-items: center; gap: 14px;
  }
  .brand__dot {
    width: 92px; height: 92px; border-radius: 50%;
    background: var(--red);
  }
  .brand__name {
    font-weight: 800; font-size: 30px; letter-spacing: 1px;
    text-transform: uppercase; color: var(--red); line-height: 1;
  }
  .card--back .brand { top: 62px; }
  .card--front .brand { top: 40px; }

  .services {
    position: absolute; left: 34px; right: 34px; bottom: 40px;
    list-style: none;
    display: flex; flex-direction: column; gap: 9px;
    font-size: 12px; font-weight: 500; line-height: 1.2;
  }
  .services__row { display: flex; flex-wrap: wrap; column-gap: 12px; row-gap: 4px; }
  .services__item { display: flex; align-items: center; gap: 7px; white-space: nowrap; }
  .services__item::before {
    content: ""; width: 6px; height: 6px; border-radius: 50%; background: var(--red); flex: none;
  }

  .person {
    position: absolute; left: 60px; bottom: 70px;
    text-align: right;
  }
  .person__name {
    font-family: "Michroma", sans-serif; font-size: 30px; letter-spacing: 1px; line-height: 1;
  }
  .person__first { color: var(--red); }
  .person__last { color: var(--ink); }
  .person__role {
    margin-top: 8px; font-size: 16px; color: var(--red); letter-spacing: 1.5px;
  }
  .divider {
    position: absolute; left: 410px; bottom: 54px;
    width: 1.5px; height: 92px; background: var(--grey);
  }
  .contact {
    position: absolute; left: 432px; bottom: 58px;
    list-style: none; display: flex; flex-direction: column; gap: 10px;
    font-size: 15px; color: var(--ink);
  }
  .contact li { display: flex; align-items: center; gap: 9px; }
  .contact svg { width: 14px; height: 14px; fill: var(--red); flex: none; }
</style>
</head>
<body>
<main class="stage">

  <section class="card card--back">
    <div class="brand">
      <span class="brand__dot"></span>
      <span class="brand__name">Copperleaf Roofing Co.</span>
    </div>
    <ul class="services">
      <li class="services__row">
        <span class="services__item">Residential &amp; commercial roofing</span>
        <span class="services__item">Storm Damage &amp; Insurance Claims specialist</span>
      </li>
      <li class="services__row">
        <span class="services__item">Roof Repairs &amp; Maintenance</span>
        <span class="services__item">Christmas Lights and permanent Christmas lights</span>
      </li>
    </ul>
  </section>

  <section class="card card--front">
    <div class="brand">
      <span class="brand__dot"></span>
      <span class="brand__name">Copperleaf Roofing Co.</span>
    </div>
    <div class="person">
      <p class="person__name"><span class="person__first">DANA</span> <span class="person__last">MERCER</span></p>
      <p class="person__role">OWNER</p>
    </div>
    <span class="divider"></span>
    <ul class="contact">
      <li>
        <svg viewBox="0 0 24 24" aria-hidden="true"><path d="M6.6 10.8a15.1 15.1 0 0 0 6.6 6.6l2.2-2.2a1 1 0 0 1 1-.25 11.4 11.4 0 0 0 3.6.57 1 1 0 0 1 1 1V20a1 1 0 0 1-1 1A17 17 0 0 1 3 4a1 1 0 0 1 1-1h3.5a1 1 0 0 1 1 1c0 1.25.2 2.45.57 3.6a1 1 0 0 1-.25 1z"/></svg>
        555-014-2290
      </li>
      <li>
        <svg viewBox="0 0 24 24" aria-hidden="true"><path d="M2 5h20v14H2z M2 5l10 8 10-8" /></svg>
        dana@copperleafroofing.co
      </li>
      <li>
        <svg viewBox="0 0 24 24" aria-hidden="true"><path d="M12 2a10 10 0 1 0 0 20 10 10 0 0 0 0-20zm6.9 6h-2.9a15.6 15.6 0 0 0-1.4-3.6A8 8 0 0 1 18.9 8zM12 4a14 14 0 0 1 1.9 4h-3.8A14 14 0 0 1 12 4zM4.3 14a8 8 0 0 1 0-4h3.4a16.5 16.5 0 0 0 0 4zm.8 2h2.9a15.6 15.6 0 0 0 1.4 3.6A8 8 0 0 1 5.1 16zM8 8H5.1a8 8 0 0 1 4.3-3.6A15.6 15.6 0 0 0 8 8zm4 12a14 14 0 0 1-1.9-4h3.8A14 14 0 0 1 12 20zm2.3-6H9.7a14.7 14.7 0 0 1 0-4h4.6a14.7 14.7 0 0 1 0 4zm.3 5.6a15.6 15.6 0 0 0 1.4-3.6h2.9a8 8 0 0 1-4.3 3.6zM16.3 14a16.5 16.5 0 0 0 0-4h3.4a8 8 0 0 1 0 4z"/></svg>
        www.copperleafroofing.co
      </li>
    </ul>
  </section>

</main>
</body>
</html>
```